BrindleStaffing Business Card Design

We are a staffing company finding positions for dedicated nurses and physicians.

Target Market(s)

Business Professionals

Industry/Entity Type

Staffing

Contact Information for Business Card

Gordon Pratley
Chairman
417 39th Avenue South
SAINT PETERSBURG FL 33712
813-555-4172 Mobile
813-555-8036 Fax
gpratley@brindlestaffing.com
www.brindlestaffing.com

Font styles to use
Sans Serif

Colors
fbee3e
f04a50
f37122

Requirements
Must have
• Logo Attached, see colors below. We'd like to see Yellow, Orange and Red.

```html
<!DOCTYPE html>
<html lang="en">
<head>
<meta charset="utf-8">
<title>BrindleStaffing Business Card</title>
<link href="https://fonts.googleapis.com/css2?family=Roboto:wght@400;500;700&display=swap" rel="stylesheet">
<style>
  :root {
    --stage: #2b2b2b;
    --yellow: #fbee3e;
    --red: #f04a50;
    --orange: #f37122;
    --white: #ffffff;
    --card-w: 540px;
    --card-h: 309px;
  }
  * { margin: 0; padding: 0; box-sizing: border-box; }
  html, body {
    width: 1200px; height: 768px; overflow: hidden;
    background: var(--stage);
    font-family: "Roboto", Arial, sans-serif;
  }
  .stage {
    width: 1200px; height: 768px;
    display: flex; align-items: center; justify-content: center; gap: 40px;
  }
  .card {
    position: relative;
    width: var(--card-w); height: var(--card-h);
    border-radius: 22px; overflow: hidden;
    box-shadow: 0 10px 30px rgba(0,0,0,.45);
  }
  /* Back face */
  .card--back { background: var(--orange); color: var(--white); }
  .card--back .brand-name {
    position: absolute; left: 0; right: 0; top: 122px;
    text-align: center; font-weight: 700; font-size: 44px; letter-spacing: -0.5px;
  }
  .card--back .website {
    position: absolute; left: 0; right: 0; bottom: 30px;
    text-align: center; font-size: 13px; letter-spacing: 5px;
  }
  /* Front face */
  .card--front { background: var(--red); color: var(--white); }
  .card__swoosh { position: absolute; inset: 0; }
  .card--front .brand-name {
    position: absolute; left: 42px; top: 40px;
    font-weight: 700; font-size: 30px; color: var(--orange); letter-spacing: -0.3px;
  }
  .contact {
    position: absolute; right: 30px; top: 38px; text-align: right;
  }
  .contact__name { font-weight: 700; font-size: 23px; line-height: 1; }
  .contact__title { font-weight: 500; font-size: 13px; margin-top: 3px; }
  .contact__address { font-size: 13.5px; line-height: 1.3; margin-top: 52px; }
  .contact__lines { margin-top: 16px; font-size: 13.5px; line-height: 1.45; }
  .contact__line { display: flex; justify-content: flex-end; align-items: center; gap: 8px; }
  .contact__line svg { width: 14px; height: 14px; flex: none; }
</style>
</head>
<body>
<main class="stage">

  <section class="card card--back" aria-label="Card back">
    <div class="brand-name">BrindleStaffing</div>
    <div class="website">www.brindlestaffing.com</div>
  </section>

  <section class="card card--front" aria-label="Card front">
    <svg class="card__swoosh" viewBox="0 0 540 309" preserveAspectRatio="none" aria-hidden="true">
      <path d="M0 0 H345 C320 170 200 262 0 276 Z" fill="var(--yellow)"/>
      <path d="M0 0 H328 C300 165 185 252 0 266 Z" fill="var(--white)"/>
    </svg>

    <div class="brand-name">BrindleStaffing</div>

    <div class="contact">
      <div class="contact__name">Gordon Pratley</div>
      <div class="contact__title">Chairman</div>
      <div class="contact__address">417 39th Avenue South<br>SAINT PETERSBURG FL 33712</div>
      <div class="contact__lines">
        <div class="contact__line">813-555-4172
          <svg viewBox="0 0 14 14"><rect x="3.5" y="1" width="7" height="12" rx="1.5" fill="none" stroke="#fff" stroke-width="1.4"/></svg>
        </div>
        <div class="contact__line">813-555-8036
          <svg viewBox="0 0 14 14"><rect x="4" y="1" width="6" height="4" fill="#fff"/><rect x="1" y="5" width="12" height="6" rx="1" fill="#fff"/><rect x="4" y="10" width="6" height="3" fill="#fff"/></svg>
        </div>
        <div class="contact__line">gpratley@brindlestaffing.com
          <svg viewBox="0 0 14 14"><rect x="1" y="3" width="12" height="8" fill="#fff"/><path d="M1 3 L7 8 L13 3" fill="none" stroke="var(--red)" stroke-width="1.2"/></svg>
        </div>
        <div class="contact__line">www.brindlestaffing.com
          <svg viewBox="0 0 14 14"><circle cx="7" cy="7" r="6" fill="#fff"/><path d="M1 7 H13 M7 1 C4 4 4 10 7 13 M7 1 C10 4 10 10 7 13" fill="none" stroke="var(--red)" stroke-width="1"/></svg>
        </div>
      </div>
    </div>
  </section>

</main>
</body>
</html>
```